Lumora Systems New Website - IT Infrastructure | Smart Cabinet | Micro Data Center

We're an IT SI providing Server Room Design & Build | All-in-One Rack & Smart Cabinet | Structured Cabling | IT Relocation | Maintenance. Old website can be found at www.lumorasys.com.hk. We'd like a brand new wix website which is modern, minimalist, interactive with some animation. Website content will be mostly static and include our service, our project, news and events, about us, contacts, blogs, partners and brands, etc.

reference sites:
We'd like to see more designs referring to below

https://www.pixelvane.example/design/41736205
https://www.pixelvane.example/design/41892417
https://velbrinn.example/

Animation (scrolling effect) referring to
https://velbrinn.example/intelligence/smart-office-room/
Updates

we'd like below style.

Designs look the same

Target Market(s)

Commercials in HK

Industry/Entity Type

IT, Technology, Data Center

Coding

Coded - Design and coding required

Font styles to use
Sans Serif

Requirements
Must have
• CMS, Some Interactive Elements/ Graphics

```html
<!DOCTYPE html>
<html lang="en">
<head>
<meta charset="utf-8">
<title>Lumora Systems – IT Infrastructure | Smart Cabinet | Micro Data Center</title>
<link href="https://fonts.googleapis.com/css2?family=Poppins:wght@500;600;700&family=Roboto:wght@400;500&display=swap" rel="stylesheet">
<style>
:root{
  --blue:#0f56a6;
  --blue-dark:#0b4a92;
  --green:#1fa58a;
  --ink:#1d1d1d;
  --muted:#666;
  --grey-bg:#f3f3f3;
  --line:#dddddd;
  --white:#fff;
}
*{box-sizing:border-box;margin:0;padding:0}
html,body{width:1200px;height:4898px;overflow:hidden}
body{position:relative;background:var(--white);font-family:'Roboto',Arial,sans-serif;color:var(--ink)}
.abs{position:absolute}
.heading{font-family:'Poppins',Arial,sans-serif;font-weight:700;color:var(--blue);font-size:42px;text-align:center;width:1200px;left:0}
.heading.light{color:var(--white)}
.rule{position:absolute;left:565px;width:70px;height:3px;background:var(--green)}

/* hero */
.hero-photo{left:0;top:0;width:1200px;height:740px;background:linear-gradient(160deg,#3a3f44 0%,#22262a 45%,#4b5158 80%,#2c3034 100%);clip-path:polygon(0 0,100% 0,100% 400px,1033px 601px,0 736px)}
.hero-accent{left:0;top:0}
.brand{left:110px;top:36px;display:flex;align-items:center;gap:10px;color:var(--white);font-family:'Poppins',Arial,sans-serif;font-weight:600;font-size:28px}
.brand-mark{width:34px;height:34px;border:3px solid var(--white);border-radius:4px}
.nav{left:498px;top:46px;display:flex;gap:30px;font-size:13px;color:var(--white);letter-spacing:.3px}
.nav .active{border-bottom:2px solid var(--white);padding-bottom:4px}
.login{left:981px;top:34px;width:107px;height:40px;background:var(--green);color:var(--white);font-size:13px;display:flex;align-items:center;justify-content:center;border-radius:2px}
.hero-title{left:115px;top:210px;font-family:'Poppins',Arial,sans-serif;font-weight:700;font-size:43px;line-height:68px;color:var(--white)}
.cta{left:116px;top:420px;width:211px;height:37px;background:var(--green);color:var(--white);font-size:13px;font-weight:500;display:flex;align-items:center;justify-content:center;border-radius:2px}
.scroll{left:588px;top:568px}

/* services */
.service{width:240px;text-align:center}
.service-photo{width:220px;height:220px;border-radius:50%;border:3px solid var(--green);margin:0 auto;padding:8px;background:var(--white)}
.service-photo span{display:block;width:100%;height:100%;border-radius:50%}
.service-label{font-family:'Poppins',Arial,sans-serif;font-weight:600;font-size:13px;line-height:21px;margin-top:14px}
.go{width:32px;height:32px;border-radius:50%;background:var(--white);box-shadow:0 2px 8px rgba(0,0,0,.18);margin:10px auto 0;display:flex;align-items:center;justify-content:center}

/* about */
.about-bg{left:0;top:1278px;width:1200px;height:678px;background:var(--grey-bg)}
.about-photo{left:57px;top:1300px;width:523px;height:656px;background:linear-gradient(180deg,#e9eef5 0%,#c9d7ea 60%,#bfc6cf 100%);clip-path:polygon(40% 0,75% 0,85% 40%,100% 60%,85% 100%,30% 100%,0 58%,25% 45%)}
.about-title{left:618px;top:1448px;font-family:'Poppins',Arial,sans-serif;font-weight:700;font-size:42px;color:var(--blue)}
.about-rule{left:619px;top:1521px;width:70px;height:3px;background:var(--green)}
.about-text{left:618px;top:1544px;width:470px;font-size:13px;line-height:23.2px;color:var(--muted);text-align:justify}

/* projects & blog cards */
.card{width:301px;height:341px;background:var(--white);box-shadow:0 3px 14px rgba(0,0,0,.14);text-align:center;padding:16px 16px 0}
.card-photo{width:269px;height:188px;display:block}
.card-title{font-family:'Poppins',Arial,sans-serif;font-weight:500;font-size:19px;line-height:26px;margin-top:22px;color:var(--ink)}
.card-link{display:inline-block;margin-top:14px;font-size:12px;font-weight:500;color:var(--green);text-decoration:underline}
.card-date{margin-top:12px;font-size:13px;color:var(--green);text-decoration:underline}
.arrow{width:32px;height:32px;border-radius:50%;background:var(--white);box-shadow:0 2px 8px rgba(0,0,0,.18);display:flex;align-items:center;justify-content:center}

/* news */
.news{width:468px;height:241px;background:var(--white);box-shadow:0 3px 14px rgba(0,0,0,.12);padding:24px 18px;display:flex;gap:22px}
.news-photo{width:139px;height:194px;flex:none}
.news-title{font-family:'Poppins',Arial,sans-serif;font-weight:500;font-size:19px;margin-top:22px}
.news-date{display:inline-flex;align-items:center;gap:6px;margin-top:10px;background:#eef7f4;color:var(--green);font-size:12px;padding:4px 10px}
.news-text{margin-top:10px;font-size:12.5px;line-height:25px;color:var(--muted)}
.dots{left:566px;top:3107px;display:flex;gap:7px}
.dots span{width:11px;height:11px;border-radius:50%;background:#cfcfcf}
.dots span.on{background:var(--green)}

/* partners */
.partners{left:110px;top:3351px;width:978px;display:grid;grid-template-columns:170px 230px 198px 205px 175px;grid-template-rows:80px 110px 91px}
.partner{display:flex;align-items:center;justify-content:center;gap:8px;font-family:'Poppins',Arial,sans-serif;font-weight:600;font-size:20px;color:#333;border-right:1px solid var(--line);border-bottom:1px solid var(--line)}
.partner:nth-child(5n){border-right:none}
.partner:nth-child(n+11){border-bottom:none}
.partner i{width:12px;height:12px;background:var(--green);display:block}

/* footer */
.footer{left:0;top:4455px;width:1200px;height:443px;background:var(--blue)}
.f-title{font-family:'Poppins',Arial,sans-serif;font-weight:600;font-size:19px;color:var(--white)}
.f-list{list-style:none;color:var(--white);font-size:13px}
.f-list li{height:26px;display:flex;align-items:center;gap:14px}
.f-contact{color:var(--white);font-size:13px;line-height:26px}
.f-contact div{display:flex;gap:14px}
.field{height:35px;border-radius:18px;background:var(--white);font-size:11px;color:#555;padding:0 22px;display:flex;align-items:center}
.message{left:622px;top:4630px;width:466px;height:86px;background:var(--white);border-radius:14px;font-size:11px;color:#555;padding:14px 22px}
.copyright{left:0;top:4792px;width:1200px;text-align:center;color:var(--white);font-size:13px}
.social{left:567px;top:4826px;display:flex;gap:6px}
.social span{width:28px;height:28px;border-radius:50%;background:var(--white)}
</style>
</head>
<body>

<!-- hero -->
<div class="abs hero-photo" role="img" aria-label="Server room aisle with rows of network cabinets"></div>
<svg class="abs hero-accent" width="1200" height="780" viewBox="0 0 1200 780">
  <polygon points="1200,409 1033,601 1200,774" fill="#1fa58a"/>
</svg>
<div class="abs brand"><span class="brand-mark"></span>Lumora</div>
<nav class="abs nav"><span class="active">HOME</span><span>SERVICES</span><span>PROJECTS</span><span>ABOUT</span><span>CONTACT</span></nav>
<div class="abs login">&#9679;&nbsp;LOGIN</div>
<h1 class="abs hero-title">IT Infrastructure<br>Smart Cabinet<br>Micro Data Center</h1>
<div class="abs cta">MAKE AN APPOINTMENT</div>
<svg class="abs scroll" width="24" height="36" viewBox="0 0 24 36">
  <circle cx="12" cy="4" r="4" fill="#1fa58a"/>
  <polyline points="5,14 12,21 19,14" fill="none" stroke="#fff" stroke-width="2.5"/>
  <polyline points="5,22 12,29 19,22" fill="none" stroke="#fff" stroke-width="2.5"/>
</svg>

<!-- services -->
<h2 class="abs heading" style="top:764px">Our Services</h2>
<div class="rule" style="top:838px"></div>
<div class="abs service" style="left:95px;top:894px">
  <div class="service-photo"><span role="img" aria-label="Data center hall with raised floor" style="background:linear-gradient(180deg,#3b3f45,#c9cdd2)"></span></div>
  <div class="service-label">Data center design<br>and build</div>
  <div class="go"><svg width="12" height="12" viewBox="0 0 12 12"><path d="M1 6h9M6 2l4 4-4 4" stroke="#1fa58a" stroke-width="2" fill="none"/></svg></div>
</div>
<div class="abs service" style="left:350px;top:894px">
  <div class="service-photo"><span role="img" aria-label="Patch panel with yellow structured cabling" style="background:linear-gradient(180deg,#27466f,#c9a52c)"></span></div>
  <div class="service-label">Structured cabling and<br>fiber backbone</div>
  <div class="go"><svg width="12" height="12" viewBox="0 0 12 12"><path d="M1 6h9M6 2l4 4-4 4" stroke="#1fa58a" stroke-width="2" fill="none"/></svg></div>
</div>
<div class="abs service" style="left:605px;top:894px">
  <div class="service-photo"><span role="img" aria-label="Technician working at an all-in-one rack" style="background:linear-gradient(180deg,#2d3238,#51657f)"></span></div>
  <div class="service-label">All-In-One Rack /<br>Micro-Data Center</div>
  <div class="go"><svg width="12" height="12" viewBox="0 0 12 12"><path d="M1 6h9M6 2l4 4-4 4" stroke="#1fa58a" stroke-width="2" fill="none"/></svg></div>
</div>
<div class="abs service" style="left:860px;top:894px">
  <div class="service-photo"><span role="img" aria-label="Conference room with ceiling lights" style="background:linear-gradient(180deg,#5b6066,#9ea39e)"></span></div>
  <div class="service-label">Audiovisual and<br>Conference Room</div>
  <div class="go"><svg width="12" height="12" viewBox="0 0 12 12"><path d="M1 6h9M6 2l4 4-4 4" stroke="#1fa58a" stroke-width="2" fill="none"/></svg></div>
</div>

<!-- about -->
<div class="abs about-bg"></div>
<svg class="abs" style="left:0;top:1278px" width="1200" height="678" viewBox="0 0 1200 678">
  <polygon points="0,0 430,0 1200,0 1200,0" fill="#f3f3f3"/>
  <polygon points="0,0 330,400 0,678" fill="#1fa58a"/>
</svg>
<div class="abs about-photo" role="img" aria-label="Smiling professional holding a laptop"></div>
<h2 class="abs about-title">About Us</h2>
<div class="abs about-rule"></div>
<p class="abs about-text">Lumora Systems is well experienced in delivering the best in Data Center Infrastructure, Network Infrastructure, Structured Cabling, Telephony, Access Control, Video Surveillance, Audiovisual &amp; Conferencing, Relocation &amp; Migration and Maintenance solutions. Our dedication, focus, and expertise wins much recognition of many IT professionals in all industries in the region. In Lumora Systems's Belief, the major reason that we gain a lot of true long-lasting business relationship with our clients was that we offer them the attention, consideration, passion, and professionalism that they deserved. With our vendor-independent expertise in best-of-breed IT infrastucture solution, not only are we to fulfill your business needs with unbiased recommendation, but we also help IT Professionals create the most cost-effective solution and best uptime that meets their ever-changing demand.</p>

<!-- projects -->
<svg class="abs" style="left:0;top:1955px" width="1200" height="682" viewBox="0 0 1200 682">
  <polygon points="0,0 1200,0 1200,518 0,680" fill="#0f56a6"/>
</svg>
<h2 class="abs heading light" style="top:2063px">Our Projects</h2>
<div class="rule" style="top:2137px"></div>
<div class="abs arrow" style="left:40px;top:2325px"><svg width="10" height="10" viewBox="0 0 10 10"><path d="M7 1L3 5l4 4" stroke="#555" stroke-width="1.6" fill="none"/></svg></div>
<div class="abs arrow" style="left:1128px;top:2325px"><svg width="10" height="10" viewBox="0 0 10 10"><path d="M3 1l4 4-4 4" stroke="#555" stroke-width="1.6" fill="none"/></svg></div>
<div class="abs card" style="left:112px;top:2177px">
  <span class="card-photo" role="img" aria-label="Network rack with blue patch cables" style="background:linear-gradient(90deg,#1e2227,#3c5d8e 50%,#1e2227)"></span>
  <div class="card-title">A renowned China<br>based listed insurance</div>
  <span class="card-link">LEARN MORE</span>
</div>
<div class="abs card" style="left:449px;top:2177px">
  <span class="card-photo" role="img" aria-label="Switch panels filled with blue cables" style="background:linear-gradient(180deg,#2e68b4,#1b3c6b 50%,#3a79c6)"></span>
  <div class="card-title">Meridian Sourcing</div>
  <span class="card-link" style="margin-top:40px">LEARN MORE</span>
</div>
<div class="abs card" style="left:787px;top:2177px">
  <span class="card-photo" role="img" aria-label="Cabinet with bundled blue cabling" style="background:linear-gradient(90deg,#121820,#2e6cc0 55%,#9aa0a6)"></span>
  <div class="card-title">Harbourline Capital &amp;<br>Eastgate Assurance</div>
  <span class="card-link">LEARN MORE</span>
</div>

<!-- news -->
<h2 class="abs heading" style="top:2681px">News And Events</h2>
<div class="rule" style="top:2756px"></div>
<div class="abs news" style="left:110px;top:2808px">
  <span class="news-photo" role="img" aria-label="Rows of server cabinets" style="background:linear-gradient(135deg,#2f3338,#b4b8bc)"></span>
  <div>
    <div class="news-title">Lorem ipsum dolor sit amet</div>
    <div class="news-date">&#9632; Dec 13,2023</div>
    <p class="news-text">Lorem ipsum dolor sit amet, consectetur adipiscing elit, sed do eiusmod tempor incididunt ut labore et dolore</p>
  </div>
</div>
<div class="abs news" style="left:620px;top:2808px">
  <span class="news-photo" role="img" aria-label="Black data center cabinets" style="background:linear-gradient(135deg,#15181c,#4a5058)"></span>
  <div>
    <div class="news-title">Lorem ipsum dolor sit amet</div>
    <div class="news-date">&#9632; Dec 13,2023</div>
    <p class="news-text">Lorem ipsum dolor sit amet, consectetur adipiscing elit, sed do eiusmod tempor incididunt ut labore et dolore</p>
  </div>
</div>
<div class="abs dots"><span></span><span class="on"></span><span></span><span></span></div>

<!-- partners -->
<h2 class="abs heading" style="top:3239px">Our Partners</h2>
<div class="rule" style="top:3313px"></div>
<div class="abs partners">
  <div class="partner"><i></i>Corvane</div>
  <div class="partner">Tessmark</div>
  <div class="partner">Kylotec</div>
  <div class="partner">Veridata</div>
  <div class="partner">Sentiphon</div>
  <div class="partner">Brisklink</div>
  <div class="partner">Halvision</div>
  <div class="partner"><i></i>Conferra</div>
  <div class="partner">Voxly</div>
  <div class="partner">Cablora</div>
  <div class="partner">Orbisoft</div>
  <div class="partner">Voltguard</div>
  <div class="partner">Alder Peak</div>
  <div class="partner">Rackwell</div>
  <div class="partner"></div>
</div>

<!-- blog -->
<svg class="abs" style="left:0;top:3700px" width="1200" height="755" viewBox="0 0 1200 755">
  <polygon points="0,110 1200,0 1200,755 0,755" fill="#f3f3f3"/>
  <polygon points="0,56 105,170 0,290" fill="#1fa58a"/>
</svg>
<h2 class="abs heading" style="top:3890px">Latest Blog</h2>
<div class="rule" style="top:3964px"></div>
<div class="abs arrow" style="left:40px;top:4150px"><svg width="10" height="10" viewBox="0 0 10 10"><path d="M7 1L3 5l4 4" stroke="#555" stroke-width="1.6" fill="none"/></svg></div>
<div class="abs arrow" style="left:1128px;top:4150px"><svg width="10" height="10" viewBox="0 0 10 10"><path d="M3 1l4 4-4 4" stroke="#555" stroke-width="1.6" fill="none"/></svg></div>
<div class="abs card" style="left:112px;top:4003px">
  <span class="card-photo" role="img" aria-label="Open server rack with cabling" style="background:linear-gradient(90deg,#1e2227,#4a6d9a 50%,#2a2e33)"></span>
  <div class="card-title">Lorem ipsum dolor sit<br>consectetur</div>
  <div class="card-date">&#9632; JAN 20,2023</div>
</div>
<div class="abs card" style="left:449px;top:4003px">
  <span class="card-photo" role="img" aria-label="Blue network cables in patch panels" style="background:linear-gradient(180deg,#2e68b4,#1b3c6b 50%,#3a79c6)"></span>
  <div class="card-title">Lorem ipsum dolor sit<br>consectetur</div>
  <div class="card-date">&#9632; JAN 20,2023</div>
</div>
<div class="abs card" style="left:787px;top:4003px">
  <span class="card-photo" role="img" aria-label="Technicians installing equipment in a server room" style="background:linear-gradient(135deg,#2b3038,#4f6ea6 60%,#8c9096)"></span>
  <div class="card-title">Lorem ipsum dolor sit<br>consectetur</div>
  <div class="card-date">&#9632; JAN 20,2023</div>
</div>

<!-- footer -->
<footer class="abs footer"></footer>
<div class="abs f-title" style="left:110px;top:4533px">Quick Links</div>
<ul class="abs f-list" style="left:110px;top:4579px">
  <li>&#187; <span>Home</span></li><li>&#187; <span>About</span></li><li>&#187; <span>Services</span></li><li>&#187; <span>Projects</span></li><li>&#187; <span>Contact</span></li>
</ul>
<div class="abs f-title" style="left:333px;top:4533px">Contact Us</div>
<div class="abs f-contact" style="left:333px;top:4579px;width:260px">
  <div><span style="color:#1fa58a">&#9679;</span><span>Rm 1508, 15/F, Crestview Centre,<br>28 Kwai Lok Street, Kwun Tong</span></div>
  <div><span style="color:#1fa58a">&#9679;</span><span>+852 3016 4470</span></div>
  <div style="margin-top:26px"><span style="color:#1fa58a">&#9632;</span><span>marketing@lumorasys.com.hk</span></div>
</div>
<div class="abs f-title" style="left:622px;top:4531px">Get In Touch</div>
<div class="abs field" style="left:622px;top:4582px;width:146px">Name</div>
<div class="abs field" style="left:782px;top:4582px;width:146px">Phone</div>
<div class="abs field" style="left:941px;top:4582px;width:147px">Email</div>
<div class="abs message">Message here..</div>
<svg class="abs" style="left:1056px;top:4690px" width="14" height="14" viewBox="0 0 14 14"><path d="M1 7l12-6-5 12-2-5z" fill="#1fa58a"/></svg>
<div class="abs copyright">© 2023 Company name &nbsp;| All Rights Reserved | Terms of Use &nbsp;| &nbsp;Privacy Policy</div>
<div class="abs social"><span></span><span></span></div>

</body>
</html>
```